Wordpress theme website for professionals working together

My partner and I are offering business services, my wife in the energy business as mainly as member of the board of commissioners. I am working as interim manager/consultant in the accounting and finance area. Both activities are connected in one company VELMOT BV (dutch ltd). We need a CV based website. Beside this we do some financial and accounting services.

Target Market(s)

small medium business

Font styles to use
Sans Serif

Colors

Designer to choose colors to be used in the design.

Requirements
Must have
• Pictures of both members.
• CLEAN AND SIMPLE
• I LIKE BLACK & WHITE
Nice to have
• I like design like this theme: http://theme.pruxelo-example.com/resume/

```html
<!DOCTYPE html>
<html lang="en">
<head>
<meta charset="utf-8">
<title>VELMOT BV — Resume Theme</title>
<link href="https://fonts.googleapis.com/css2?family=Poppins:wght@400;500;600;700&family=Mulish:wght@400;600;700&display=swap" rel="stylesheet">
<style>
:root{
  --stage:#3b3b3b;
  --paper:#ffffff;
  --ink:#1d1d1d;
  --text:#4a4a4a;
  --muted:#9a9a9a;
  --rule:#e3e3e3;
  --rail:#e9e9e9;
  --accent:#2f6fe0;
  --accent-soft:#c9dafa;
}
*{box-sizing:border-box;margin:0;padding:0}
html,body{width:1200px;height:3488px;overflow:hidden;background:var(--stage)}
body{font-family:'Mulish',sans-serif;color:var(--text);position:relative}
.screen{position:absolute;left:28px;width:1144px;height:544px;background:var(--paper);overflow:hidden}
.s1{top:28px}.s2{top:598px}.s3{top:1163px}.s4{top:1728px}.s5{top:2295px}.s6{top:2863px}

/* sidebar */
.sidebar{position:absolute;left:0;top:0;width:143px;height:100%;background:var(--paper);border-right:8px solid var(--rail);text-align:center;z-index:2}
.avatar{position:absolute;left:23px;top:37px;width:70px;height:70px;background:linear-gradient(160deg,#8b8b8b,#4e4e4e)}
.who{position:absolute;left:0;width:135px;top:109px;font-family:'Poppins',sans-serif;color:var(--ink)}
.who .name{font-size:14px;font-weight:700;line-height:19px}
.who .role{font-size:12px;font-weight:600;line-height:19px}
.who .switch{font-size:11px;font-weight:700;color:var(--accent);margin-top:10px;line-height:14px}
.nav{position:absolute;left:0;width:135px;top:195px;list-style:none}
.nav li{height:38px;border-top:1px solid var(--rule);font-family:'Poppins',sans-serif;font-size:13px;color:var(--ink);line-height:37px;position:relative}
.nav li:last-child{border-bottom:1px solid var(--rule)}
.nav li.active::after{content:"";position:absolute;right:-8px;top:0;width:3px;height:100%;background:var(--ink)}
.social{position:absolute;left:22px;top:455px;display:flex;gap:10px}
.social span{width:14px;height:14px;border-radius:50%;border:1.5px solid var(--ink)}
.copy{position:absolute;left:18px;top:490px;width:100px;text-align:left;font-size:11px;line-height:15px;color:var(--text)}
.s1 .who{top:137px}.s1 .avatar{top:40px}.s1 .nav{top:210px}

/* content */
.content{position:absolute;left:195px;top:0;width:877px;height:100%}
.title{position:absolute;left:0;top:28px;width:877px;font-family:'Poppins',sans-serif;font-size:25px;font-weight:600;color:var(--ink);padding-bottom:10px;border-bottom:1px solid var(--rule)}
.sub{font-family:'Poppins',sans-serif;font-size:15px;font-weight:500;color:var(--ink);display:inline-block;padding-bottom:6px;border-bottom:2px solid var(--accent)}
p.body{font-size:12.5px;line-height:20px;color:var(--text)}

/* hero */
.hero{position:absolute;left:135px;top:0;right:0;height:100%;background:linear-gradient(120deg,#5b4f47 0%,#8a7c70 35%,#3c3a3a 70%,#24201f 100%)}
.hero-copy{position:absolute;left:135px;right:0;top:175px;text-align:center;color:#fff}
.hero h1{font-family:'Poppins',sans-serif;font-size:40px;font-weight:600;letter-spacing:1px}
.hero-copy p{font-family:'Poppins',sans-serif;font-size:16px;font-weight:500;line-height:32px;width:640px;margin:14px auto 0}
.btns{display:flex;justify-content:center;gap:16px;margin-top:38px}
.btn{display:flex;align-items:center;justify-content:center;gap:8px;height:48px;border:3px solid #fff;border-radius:26px;font-family:'Poppins',sans-serif;font-weight:600;font-size:16px;color:#fff}
.btn.read{width:204px}.btn.contact{width:178px}

/* about */
.portrait{position:absolute;left:48px;top:101px;width:174px;height:174px;border-radius:50%;border:3px solid var(--accent);padding:6px}
.portrait div{width:100%;height:100%;border-radius:50%;background:linear-gradient(160deg,#b7b7b7,#5f5f5f)}
.about-intro{position:absolute;left:312px;top:97px;width:560px}
.about-intro h3{font-family:'Poppins',sans-serif;font-size:16px;font-weight:500;color:var(--ink);margin-bottom:12px}
.about-intro p{margin-bottom:16px}
.jobs{position:absolute;left:0;top:300px;width:540px}
.jobs p{margin-top:16px}
.facts{position:absolute;left:582px;top:303px;width:290px;font-size:12.5px}
.facts .row{display:flex;height:30.4px;align-items:flex-start}
.facts .k{width:98px;font-family:'Poppins',sans-serif;font-weight:600;color:var(--ink);display:flex;gap:5px;align-items:center}
.facts .k em{font-style:normal;border-bottom:2px solid var(--accent);padding-bottom:2px}
.facts svg{width:12px;height:12px}

/* resume */
.col-left{position:absolute;left:0;top:88px;width:560px}
.tl{position:relative;margin:18px 0 0}
.tl-item{display:flex;position:relative;margin-bottom:28px}
.tl-item .when{width:157px;text-align:right;font-size:12.5px;line-height:18px;color:var(--text)}
.tl-item .dot{width:42px;position:relative}
.tl-item .dot::before{content:"";position:absolute;left:15px;top:4px;width:8px;height:8px;border-radius:50%;border:2px solid var(--accent);background:#fff}
.tl-item .what{width:345px;font-size:12.5px;line-height:20px}
.tl-item .what b{display:block;font-family:'Poppins',sans-serif;font-size:13px;font-weight:600;color:var(--ink);line-height:18px;margin-bottom:4px}
.tl::before{content:"";position:absolute;left:176px;top:0;bottom:20px;width:1px;background:var(--rule)}
.skills{position:absolute;left:612px;top:88px;width:265px}
.skill{margin-top:18px}
.skill .lab{display:flex;justify-content:space-between;font-family:'Poppins',sans-serif;font-size:11px;font-weight:600;color:var(--ink)}
.skill .lab span{font-family:'Mulish',sans-serif;font-weight:400;color:var(--muted)}
.bar{height:6px;background:var(--accent-soft);border-radius:3px;margin-top:5px;overflow:hidden}
.bar i{display:block;height:100%;background:var(--accent)}

/* portfolio */
.filters{position:absolute;right:0;top:85px;display:flex;gap:20px;font-family:'Poppins',sans-serif;font-size:14px;color:var(--ink)}
.filters .on{border:1px solid var(--ink);padding:0 5px}
.grid{position:absolute;left:0;top:130px;display:grid;grid-template-columns:repeat(3,285px);grid-template-rows:repeat(2,196px);gap:8px 11px}
.ph{display:block}
.g1{background:linear-gradient(135deg,#c89a62,#3d3026)}
.g2{background:linear-gradient(160deg,#8fa8c8,#2f3b4d)}
.g3{background:linear-gradient(140deg,#a9c7e0,#3b5a78)}
.g4{background:linear-gradient(150deg,#d9d5cf,#7d756b)}
.g5{background:linear-gradient(140deg,#e8e8ea,#8d97a6)}
.g6{background:linear-gradient(150deg,#eef2f8,#9cb1cf)}

/* blog */
.posts{position:absolute;left:0;top:77px;display:grid;grid-template-columns:repeat(2,392px);gap:10px 10px}
.post{border:1px solid var(--rule);height:222px}
.post .ph{height:158px}
.post .date{font-size:10px;color:var(--muted);margin:10px 10px 0}
.post h4{font-family:'Poppins',sans-serif;font-size:12.5px;font-weight:600;color:var(--ink);margin:6px 10px 0}
.b1{background:linear-gradient(150deg,#d9dde4,#6b7380)}
.b2{background:linear-gradient(150deg,#c7cdd6,#4b5260)}
.b3{background:linear-gradient(150deg,#cfd3d8,#3e4652)}
.b4{background:linear-gradient(150deg,#5a6370,#d9dde3)}

/* contact */
.map{position:absolute;left:0;top:109px;width:877px;height:245px;background:linear-gradient(135deg,#ececec,#dcdedf)}
.cards{position:absolute;left:0;top:388px;width:877px;display:grid;grid-template-columns:repeat(4,1fr);gap:26px}
.card{height:112px;border:1px solid var(--rule);box-shadow:0 2px 6px rgba(0,0,0,.12);display:flex;flex-direction:column;align-items:center;justify-content:center;gap:10px;font-size:19px;color:var(--ink);white-space:nowrap}
.card svg{width:26px;height:26px}
</style>
</head>
<body>

<!-- 1: Home -->
<section class="screen s1">
  <aside class="sidebar">
    <div class="avatar" role="img" aria-label="Portrait photo of Marten"></div>
    <div class="who"><div class="name">MARTEN</div><div class="role">Advisor WMD</div></div>
    <ul class="nav"><li class="active">Home</li><li>About me</li><li>Resume</li><li>Portfolio</li><li>Blog</li><li>Contact Us</li></ul>
    <div class="social"><span></span><span></span><span></span></div>
    <div class="copy">© 2018 All rights reserved.</div>
  </aside>
  <div class="hero" role="img" aria-label="Photo of hands working on a calculator and documents at a desk"></div>
  <div class="hero-copy">
    <h1>WELCOME TO VELMOT BV</h1>
    <p>Sed ut perspiciatis unde omnis iste natus error sit voluptatem accusantium doloremque</p>
    <div class="btns">
      <div class="btn read"><svg width="14" height="16" viewBox="0 0 14 16"><path d="M1 1h8l4 4v10H1z" fill="#fff"/></svg>Read More</div>
      <div class="btn contact"><svg width="16" height="16" viewBox="0 0 16 16"><path d="M15 1L1 7l6 2 2 6z" fill="none" stroke="#fff" stroke-width="2" stroke-linejoin="round"/></svg>Contact us</div>
    </div>
  </div>
</section>

<!-- 2: About -->
<section class="screen s2">
  <aside class="sidebar">
    <div class="avatar" role="img" aria-label="Portrait photo of Marten"></div>
    <div class="who"><div class="name">MARTEN</div><div class="role">Advisor WMD</div><div class="switch">Switch to Ilse</div></div>
    <ul class="nav"><li>Home</li><li class="active">About me</li><li>Resume</li><li>Portfolio</li><li>Blog</li><li>Contact Us</li></ul>
    <div class="social"><span></span><span></span><span></span></div>
    <div class="copy">© 2018 All rights reserved.</div>
  </aside>
  <div class="content">
    <h2 class="title">About Me</h2>
    <div class="portrait"><div role="img" aria-label="Round portrait photo of Marten"></div></div>
    <div class="about-intro">
      <h3>I am Advisor WMD</h3>
      <p class="body">Praesent ut tortor consectetur, semper sapien non, lacinia augue. Aenean arcu libero, facilisis et nisi non, tempus faucibus tortor. Mauris vel nulla aliquam, pellentesque enim ac, faucibus tortor. Nulla odio nibh, cursus sit amet urna id, dignissim euismod augue.</p>
      <p class="body">Praesent ut tortor consectetur, semper sapien non, lacinia augue. Aenean arcu libero, facilisis et nisi non, tempus faucibus tortor. Mauris vel nulla aliquam, pellentesque enim ac, faucibus tortor. Nulla odio nibh, cursus sit amet urna id, dignissim euismod augue.</p>
    </div>
    <div class="jobs">
      <h3 class="sub">Finished jobs: Controller a.i. WMD</h3>
      <p class="body">Praesent ut tortor consectetur, semper sapien non, lacinia augue. Aenean arcu libero, facilisis et nisi non, tempus faucibus tortor. Mauris vel nulla aliquam, pellentesque enim ac, faucibus tortor. Nulla odio nibh, cursus sit amet urna id, dignissim euismod augue.</p>
      <p class="body">Praesent ut tortor consectetur, semper sapien non, lacinia augue. Aenean arcu libero, facilisis et nisi non, tempus faucibus tortor. Mauris vel nulla aliquam, pellentesque enim ac, faucibus tortor. Nulla odio nibh, cursus sit amet urna id, dignissim euismod augue.</p>
    </div>
    <div class="facts">
      <div class="row"><div class="k"><svg viewBox="0 0 12 12"><circle cx="6" cy="3.5" r="2.5" fill="#1d1d1d"/><path d="M1 12c0-4 10-4 10 0z" fill="#1d1d1d"/></svg><em>Age</em></div><div>29</div></div>
      <div class="row"><div class="k"><svg viewBox="0 0 12 12"><rect x="2" y="1" width="8" height="11" fill="#1d1d1d"/></svg><em>Residence</em></div><div>USA</div></div>
      <div class="row"><div class="k"><svg viewBox="0 0 12 12"><path d="M6 12S1.5 7 1.5 4.5a4.5 4.5 0 019 0C10.5 7 6 12 6 12z" fill="#1d1d1d"/><circle cx="6" cy="4.5" r="1.6" fill="#fff"/></svg><em>Address</em></div><div>88 Some Street, Some Town</div></div>
      <div class="row"><div class="k"><svg viewBox="0 0 12 12"><rect x="1" y="2.5" width="10" height="7.5" fill="none" stroke="#1d1d1d" stroke-width="1.4"/><path d="M1 3l5 4 5-4" fill="none" stroke="#1d1d1d" stroke-width="1.4"/></svg><em>e-mail</em></div><div>email@example.com</div></div>
      <div class="row"><div class="k"><svg viewBox="0 0 12 12"><path d="M2 1h3l1 3-2 1c1 2 2 3 3 3l1-2 3 1v3c-6 1-10-4-9-9z" fill="#1d1d1d"/></svg><em>Phone</em></div><div>+0123 123 456 789</div></div>
      <div class="row"><div class="k"><svg viewBox="0 0 12 12"><circle cx="6" cy="6" r="5" fill="none" stroke="#1d1d1d" stroke-width="1.4"/></svg><em>Skype</em></div><div>Marten</div></div>
    </div>
  </div>
</section>

<!-- 3: Resume -->
<section class="screen s3">
  <aside class="sidebar">
    <div class="avatar" role="img" aria-label="Portrait photo of Marten"></div>
    <div class="who"><div class="name">MARTEN</div><div class="role">Advisor WMD</div><div class="switch">Switch to Ilse</div></div>
    <ul class="nav"><li>Home</li><li>About me</li><li class="active">Resume</li><li>Portfolio</li><li>Blog</li><li>Contact Us</li></ul>
    <div class="social"><span></span><span></span><span></span></div>
    <div class="copy">© 2018 All rights reserved.</div>
  </aside>
  <div class="content">
    <h2 class="title">Resume</h2>
    <div class="col-left">
      <h3 class="sub">Education</h3>
      <div class="tl">
        <div class="tl-item"><div class="when">2000<br>University of Studies</div><div class="dot"></div><div class="what"><b>Norvia (RA)</b>Maecenas finibus nec sem ut imperdiet. Ut tincidunt est ac dolor aliquam sodales.</div></div>
        <div class="tl-item"><div class="when">1997<br>University of Studies</div><div class="dot"></div><div class="what"><b>Atheneum B</b>Maecenas finibus nec sem ut imperdiet. Ut tincidunt est ac dolor aliquam sodales.</div></div>
      </div>
      <h3 class="sub" style="margin-top:-4px">Worked for</h3>
      <div class="tl">
        <div class="tl-item" style="margin-bottom:40px"><div class="when">2002 - 2016<br>Designation</div><div class="dot"></div><div class="what"><b>Trent Advocaten &amp; Notarissen</b>Maecenas finibus nec sem ut imperdiet. Ut tincidunt est ac dolor aliquam sodales.</div></div>
        <div class="tl-item"><div class="when">2016 - Current<br>Designation</div><div class="dot"></div><div class="what"><b>Korvan Audit</b>Maecenas finibus nec sem ut imperdiet. Ut tincidunt est ac dolor aliquam sodales.</div></div>
      </div>
    </div>
    <div class="skills">
      <h3 class="sub">Skills</h3>
      <div class="skill"><div class="lab">Annual reporting<span>60%</span></div><div class="bar"><i style="width:60%"></i></div></div>
      <div class="skill"><div class="lab">Financial monthly reporting<span>60%</span></div><div class="bar"><i style="width:60%"></i></div></div>
      <div class="skill"><div class="lab">Accounting<span>100%</span></div><div class="bar"><i style="width:100%"></i></div></div>
      <div class="skill"><div class="lab">Financial management<span>60%</span></div><div class="bar"><i style="width:60%"></i></div></div>
      <div class="skill"><div class="lab">Project management<span>60%</span></div><div class="bar"><i style="width:60%"></i></div></div>
      <div class="skill"><div class="lab">Team player<span>100%</span></div><div class="bar"><i style="width:100%"></i></div></div>
      <div class="skill"><div class="lab">Trouble shooter<span>60%</span></div><div class="bar"><i style="width:60%"></i></div></div>
    </div>
  </div>
</section>

<!-- 4: Portfolio -->
<section class="screen s4">
  <aside class="sidebar">
    <div class="avatar" role="img" aria-label="Portrait photo of Marten"></div>
    <div class="who"><div class="name">MARTEN</div><div class="role">Advisor WMD</div><div class="switch">Switch to Ilse</div></div>
    <ul class="nav"><li>Home</li><li>About me</li><li>Resume</li><li class="active">Portfolio</li><li>Blog</li><li>Contact Us</li></ul>
    <div class="social"><span></span><span></span><span></span></div>
    <div class="copy">© 2018 All rights reserved.</div>
  </aside>
  <div class="content">
    <h2 class="title">Portfolio</h2>
    <div class="filters"><span class="on">All</span><span>Fotography</span><span>Financing</span><span>Report</span></div>
    <div class="grid">
      <div class="ph g1" role="img" aria-label="Photo of a person holding a camera"></div>
      <div class="ph g2" role="img" aria-label="Photo of stacked coins"></div>
      <div class="ph g3" role="img" aria-label="Photo of glass office towers"></div>
      <div class="ph g4" role="img" aria-label="Photo of a calculator and papers on a desk"></div>
      <div class="ph g5" role="img" aria-label="Photo of a laptop with financial charts"></div>
      <div class="ph g6" role="img" aria-label="Photo of printed business charts"></div>
    </div>
  </div>
</section>

<!-- 5: Blog -->
<section class="screen s5">
  <aside class="sidebar">
    <div class="avatar" role="img" aria-label="Portrait photo of Marten"></div>
    <div class="who"><div class="name">MARTEN</div><div class="role">Advisor WMD</div><div class="switch">Switch to Ilse</div></div>
    <ul class="nav"><li>Home</li><li>About me</li><li>Resume</li><li>Portfolio</li><li class="active">Blog</li><li>Contact Us</li></ul>
    <div class="social"><span></span><span></span><span></span></div>
    <div class="copy">© 2018 All rights reserved.</div>
  </aside>
  <div class="content">
    <h2 class="title">Blog</h2>
    <div class="posts">
      <article class="post"><div class="ph b1" role="img" aria-label="Photo of hands on a laptop and calculator"></div><div class="date">06 NOV 2018</div><h4>Sed ut perspiciatis unde omnis iste natus error</h4></article>
      <article class="post"><div class="ph b2" role="img" aria-label="Photo of a person typing on a laptop"></div><div class="date">06 NOV 2018</div><h4>Sed ut perspiciatis unde omnis iste natus error</h4></article>
      <article class="post"><div class="ph b3" role="img" aria-label="Photo of a calculator on financial papers"></div><div class="date">06 NOV 2018</div><h4>Sed ut perspiciatis unde omnis iste natus error</h4></article>
      <article class="post"><div class="ph b4" role="img" aria-label="Photo of hands reviewing documents"></div><div class="date">06 NOV 2018</div><h4>Sed ut perspiciatis unde omnis iste natus error</h4></article>
    </div>
  </div>
</section>

<!-- 6: Contact -->
<section class="screen s6">
  <aside class="sidebar">
    <div class="avatar" role="img" aria-label="Portrait photo of Marten"></div>
    <div class="who"><div class="name">MARTEN</div><div class="role">Advisor WMD</div><div class="switch">Switch to Ilse</div></div>
    <ul class="nav"><li>Home</li><li>About me</li><li>Resume</li><li>Portfolio</li><li>Blog</li><li class="active">Contact Us</li></ul>
    <div class="social"><span></span><span></span><span></span></div>
    <div class="copy">© 2018 All rights reserved.</div>
  </aside>
  <div class="content">
    <h2 class="title">Contact</h2>
    <div class="map" role="img" aria-label="Street map of the office location"></div>
    <div class="cards">
      <div class="card"><svg viewBox="0 0 24 24"><path d="M4 2h5l2 5-3 2c1.5 3 4 5.5 7 7l2-3 5 2v5c-10 2-20-8-18-18z" fill="#1d1d1d"/></svg>888 888 8888</div>
      <div class="card"><svg viewBox="0 0 24 24"><path d="M12 23S4 14 4 9a8 8 0 0116 0c0 5-8 14-8 14z" fill="#1d1d1d"/><circle cx="12" cy="9" r="3" fill="#fff"/></svg>San Francisco</div>
      <div class="card"><svg viewBox="0 0 24 24"><rect x="2" y="5" width="20" height="14" fill="#1d1d1d"/><path d="M2 5l10 8 10-8" fill="none" stroke="#fff" stroke-width="2"/></svg>San Francisco</div>
      <div class="card"><svg viewBox="0 0 24 24"><path d="M9 2h6v8h4l-7 7-7-7h4z" fill="#1d1d1d"/><rect x="3" y="19" width="18" height="3" fill="#1d1d1d"/></svg>Download CV</div>
    </div>
  </div>
</section>

</body>
</html>
```